Business Card Design

Online clothing womens clothing store, I sell my clothing online and at the markets.

i would like the attached picture on the front of the card and the contact information on the back.

Industry/Entity Type

Business

Contact Information for Business Card

Marlow Thread
Karen Whitfield
(Instagram symbol) _marlow_thread_
(Facebook symbol) www.fakebookexample.com/marlowthreadau/

W : www.marlowthread.example.au
E : info@marlowthread.example.au
P : 0498716204

```html
<!DOCTYPE html>
<html lang="en">
<head>
<meta charset="utf-8">
<title>Marlow Thread – Business Card</title>
<link href="https://fonts.googleapis.com/css2?family=Open+Sans:wght@400;600;700&display=swap" rel="stylesheet">
<style>
  :root {
    --page-bg: #e9e6e1;
    --card-white: #ffffff;
    --ink-black: #0d0d0d;
    --ink-grey: #4a4a4a;
    --band-grey: #6f6f6f;
    --mist-light: #dfe4e5;
    --mist-mid: #aebabd;
    --mist-dark: #3f4a4f;
    --wordmark: #ffffff;
  }
  * { box-sizing: border-box; margin: 0; padding: 0; }
  html, body {
    width: 1200px; height: 900px; overflow: hidden;
    background: var(--page-bg);
    font-family: "Open Sans", Arial, sans-serif;
  }
  .card-set {
    position: absolute; inset: 0;
    display: flex; align-items: center; justify-content: center; gap: 40px;
  }
  .card {
    position: relative; width: 540px; height: 330px; overflow: hidden;
    background: var(--card-white);
    box-shadow: 0 6px 18px rgba(0,0,0,0.18);
  }

  /* Front */
  .front-photo {
    position: absolute; inset: 0;
    background:
      radial-gradient(ellipse 55% 60% at 72% 62%, var(--mist-dark) 0%, rgba(63,74,79,0.55) 45%, rgba(63,74,79,0) 75%),
      linear-gradient(135deg, var(--mist-light) 0%, #cfd7d9 40%, var(--mist-mid) 100%);
  }
  .front-wordmark {
    position: absolute; left: 38px; bottom: 42px;
    color: var(--wordmark);
    font-weight: 700; font-size: 50px; line-height: 1;
    letter-spacing: 3px; text-transform: uppercase;
  }

  /* Back */
  .back-graphics { position: absolute; inset: 0; }
  .holder-name {
    position: absolute; left: 66px; top: 40px;
    font-weight: 700; font-size: 17px; color: var(--ink-black);
  }
  .contact-list, .social-list {
    position: absolute; left: 26px; list-style: none;
    font-size: 13.5px; color: var(--ink-grey); line-height: 20px;
  }
  .contact-list { top: 128px; }
  .social-list { top: 196px; }
  .contact-list li, .social-list li { display: flex; align-items: center; gap: 9px; }
  .contact-icon { width: 11px; height: 11px; flex: none; }
  .social-mark { width: 10px; height: 10px; flex: none; background: var(--ink-black); border-radius: 2px; }
</style>
</head>
<body>
<main class="card-set">

  <section class="card card-front">
    <div class="front-photo" role="img" aria-label="Misty grey-blue photograph of a woman in soft smoke, supplied by the client"></div>
    <div class="front-wordmark">Marlow Thread</div>
  </section>

  <section class="card card-back">
    <svg class="back-graphics" width="540" height="330" viewBox="0 0 540 330" aria-hidden="true">
      <rect x="0" y="10" width="52" height="34" fill="var(--band-grey)"/>
      <polygon points="28,44 44,10 56,10 52,44" fill="var(--ink-black)"/>
      <polygon points="0,240 296,240 290,262 0,262" fill="var(--band-grey)"/>
      <polygon points="300,262 540,262 540,330 290,330 300,262" fill="var(--ink-black)"/>
      <polygon points="296,240 304,240 294,262 290,262" fill="var(--card-white)"/>
    </svg>

    <h1 class="holder-name">Karen Whitfield</h1>

    <ul class="contact-list">
      <li>
        <svg class="contact-icon" viewBox="0 0 12 12" aria-hidden="true"><path d="M2 1h3l1 3-2 1a7 7 0 0 0 3 3l1-2 3 1v3a1 1 0 0 1-1 1A10 10 0 0 1 1 2a1 1 0 0 1 1-1z" fill="var(--ink-black)"/></svg>
        <span>0498716204</span>
      </li>
      <li>
        <svg class="contact-icon" viewBox="0 0 12 12" aria-hidden="true"><rect x="0.5" y="2" width="11" height="8" fill="var(--ink-black)"/><path d="M1 3l5 4 5-4" stroke="#fff" fill="none"/></svg>
        <span>info@marlowthread.example.au</span>
      </li>
      <li>
        <svg class="contact-icon" viewBox="0 0 12 12" aria-hidden="true"><path d="M5 7l2-2M4 5L2.5 6.5a2 2 0 0 0 3 3L7 8M8 7l1.5-1.5a2 2 0 0 0-3-3L5 4" stroke="var(--ink-black)" stroke-width="1.4" fill="none" stroke-linecap="round"/></svg>
        <span>www.marlowthread.example.au</span>
      </li>
    </ul>

    <ul class="social-list">
      <li><span class="social-mark"></span><span>_marlow_thread_</span></li>
      <li><span class="social-mark"></span><span>www.fakebookexample.com/marlowthreadau/</span></li>
    </ul>
  </section>

</main>
</body>
</html>
```